Law Firm Website

We are a small California based law firm specializing in business, corporate and litigation matters. We need to have our website redesigned. We are looking for a new and fresh look for our site, keeping in mind that we are a law firm.
What we don't want:
**the traditional "gavel" and "scales of justice" look
**anything too crazy
What we do want:
**sophisticated yet modern and fresh corporate look and feel
**samples of websites we really like:
http://www.tarnwellhope.example
http://www.marrowgate.example/
we also like:
http://www.fenwoodastley.example/
http://www.qz.example/
http://www.brenhollow.example/
http://www.pvdn.example
http://www.nqrlaw.example/
The content will be whatever is currently on our website (www.okabelawgroup.example). We will be selecting the winner based on originality and keeping the above requirements in mind. Please note that the photos that you use will be the ones that we will be using, so choose wisely because the photos will make a difference.
Target Market(s)
Corporate clients
Industry/Entity Type
Law Firm
Look and feel

```html
<!DOCTYPE html>
<html lang="pl">
<head>
<meta charset="utf-8">
<title>Okabe Law Group, LLP</title>
<link href="https://fonts.googleapis.com/css2?family=Open+Sans:wght@400;600;700&display=swap" rel="stylesheet">
<style>
  :root {
    --paper: #f3f1f2;
    --ink: #050505;
    --rule: #c9c9c9;
    --muted: #6b6b6b;
    --footer-bg: #000000;
    --footer-text: #9a9a9a;
    --footer-dim: #5e5e5e;
    --brand-blue: #1a86dc;
    --visual-light: #d9d7d8;
    --visual-mid: #a9a8a9;
    --visual-dark: #6e6d6e;
  }
  * { box-sizing: border-box; margin: 0; padding: 0; }
  html, body { width: 1200px; height: 808px; overflow: hidden; }
  body {
    position: relative;
    background: var(--paper);
    font-family: "Open Sans", Arial, sans-serif;
    color: var(--ink);
  }
  .top-bar { position: absolute; left: 0; top: 0; width: 1200px; height: 7.5px; background: var(--ink); }

  .brand-square {
    position: absolute; left: 118px; top: 33px; width: 70px; height: 70px;
    background: linear-gradient(135deg, #6fc0f5, var(--brand-blue));
  }
  .brand-name {
    position: absolute; left: 82px; top: 106px; white-space: nowrap;
    font-weight: 700; font-size: 14.5px; letter-spacing: -0.3px; color: var(--ink);
  }

  .enquiries { position: absolute; left: 848px; top: 19px; }
  .enquiries svg { position: absolute; left: 0; top: 2px; }
  .enquiries-label { position: absolute; left: 29px; top: 0; white-space: nowrap; font-size: 14px; color: var(--muted); }
  .enquiries-number { position: absolute; left: 29px; top: 13px; white-space: nowrap; font-size: 20px; color: #333; }
  .globe { position: absolute; left: 1036px; top: 19px; }

  .nav-rule { position: absolute; left: 0; top: 0; }
  .main-nav a {
    position: absolute; top: 100px; transform: translateX(-50%);
    font-weight: 700; font-size: 15px; color: var(--ink); text-decoration: none; white-space: nowrap;
  }

  .hero-visual {
    position: absolute; left: 0; top: 170px; width: 675px; height: 528px;
    background:
      linear-gradient(180deg, var(--paper) 0%, rgba(243,241,242,0) 18%),
      linear-gradient(90deg, var(--visual-light) 0%, var(--visual-mid) 25%, var(--visual-dark) 50%, var(--visual-mid) 72%, var(--visual-light) 88%, var(--paper) 100%);
  }

  .hero-title {
    position: absolute; left: 630px; top: 268px;
    text-transform: uppercase; font-weight: 600; white-space: nowrap;
  }
  .hero-title .line-big { display: block; font-size: 112px; line-height: 100px; letter-spacing: -2px; }
  .hero-title .line-small { display: block; font-size: 62px; line-height: 52px; letter-spacing: -1px; }
  .hero-text { position: absolute; left: 630px; top: 485px; width: 420px; font-size: 17.5px; line-height: 22px; }

  .site-footer { position: absolute; left: 0; top: 697.5px; width: 1200px; height: 110.5px; background: var(--footer-bg); }
  .footer-contact { position: absolute; left: 129px; top: 24px; color: var(--footer-text); }
  .footer-contact h2 { font-size: 16px; font-weight: 700; line-height: 20px; }
  .footer-contact p { font-size: 12px; line-height: 20px; padding-left: 2px; }
  .footer-contact p span { font-size: 15px; }
  .footer-contact p.phone span { font-size: 18px; }
  .footer-divider { position: absolute; left: 355px; top: 20px; width: 1px; height: 62px; background: #333; }
  .social { position: absolute; left: 399px; top: 35px; display: flex; gap: 6px; }
  .social a { display: block; width: 33px; height: 33px; border-radius: 50%; background: #7a7a7a; }
  .copyright { position: absolute; right: 133px; top: 42px; font-size: 14px; color: var(--footer-dim); white-space: nowrap; }
</style>
</head>
<body>
  <div class="top-bar"></div>

  <header>
    <span class="brand-square"></span>
    <span class="brand-name">Okabe Law Group, LLP</span>

    <div class="enquiries">
      <svg width="20" height="30" viewBox="0 0 20 30" aria-hidden="true">
        <rect x="1" y="1" width="18" height="28" rx="3" fill="#111"/>
        <rect x="4" y="5" width="12" height="18" fill="#f3f1f2"/>
        <rect x="7" y="2.5" width="6" height="1.2" fill="#f3f1f2"/>
      </svg>
      <span class="enquiries-label">call us for enquiries</span>
      <span class="enquiries-number">005550148821</span>
    </div>

    <svg class="globe" width="32" height="32" viewBox="0 0 32 32" aria-label="Język">
      <circle cx="16" cy="16" r="14.5" fill="#111"/>
      <circle cx="16" cy="16" r="12" fill="none" stroke="#f3f1f2" stroke-width="1.3"/>
      <ellipse cx="16" cy="16" rx="5" ry="12" fill="none" stroke="#f3f1f2" stroke-width="1.3"/>
      <line x1="4" y1="16" x2="28" y2="16" stroke="#f3f1f2" stroke-width="1.3"/>
    </svg>

    <svg class="nav-rule" width="1200" height="140" aria-hidden="true">
      <polyline points="242,126.5 664,126.5 678,93 820,93 834,126.5 975,126.5 989,93 1200,91"
                fill="none" stroke="var(--rule)" stroke-width="2"/>
    </svg>

    <nav class="main-nav">
      <a href="#" style="left:629px">O NAS</a>
      <a href="#" style="left:753px">INDYWIDUALNI</a>
      <a href="#" style="left:905px">KORPORACYJNI</a>
      <a href="#" style="left:1032px">KONTAKT</a>
    </nav>
  </header>

  <main>
    <div class="hero-visual" role="img" aria-label="Black and white sketch of a blindfolded justice statue holding scales, with diagonal hatched strokes"></div>
    <h1 class="hero-title">
      <span class="line-big">What</span>
      <span class="line-small">Makes us</span>
      <span class="line-small">Different ?</span>
    </h1>
    <p class="hero-text">We have a one-on-one, very personal approach that isn't typical of many client-attorney relationships.</p>
  </main>

  <footer class="site-footer">
    <div class="footer-contact">
      <h2>OKABE LAW CENTRE</h2>
      <p>E-MAIL: <span>info@okabelaw.example</span></p>
      <p class="phone">PHONE: <span>555 010 4821</span></p>
    </div>
    <div class="footer-divider"></div>
    <div class="social">
      <a href="#" aria-label="Social profile one"></a>
      <a href="#" aria-label="Social profile two"></a>
      <a href="#" aria-label="Social profile three"></a>
    </div>
    <p class="copyright">© Copyright 2014 . All rights reserved to okabe law centre</p>
  </footer>
</body>
</html>
```